Postcard Design

business name: COZY HOUR HELPER. I am a mother of 2 well adjusted, successful teenage boys. I decided to start this company caring for kids who are home sick, unable to go to daycare or school, and when their parent cant stay home with them. I was also a career woman for many years, with no friends available or family nearby to help when i was in an emergency situation for childcare. I know how stressful it can be when a child gets sick suddenly and unexpectedly. I would like to help out those parents in need, that have pressing schedules and a sick child at home that they really want to take care of, but cant due to their work pressures and priorities. I want parents to know that their child is safe and I can help them when in need, at last minute. The design should show the child is safe and well cared for and the parent is at ease, able to accomplish their obligations. I have also founded a nonprofit environmental education program in which I teach children in youth summer camps. I have taught creativity arts combined with science curriculum in kindergarten to 8th grade non-formal teaching for the past 5 years. This is a small community, and many people know me. I will be handing out these postcards to local daycares and people I know.

Industry/Entity Type

Business

```html
<!DOCTYPE html>
<html lang="en">
<head>
<meta charset="utf-8">
<title>Cozy Hour Helper – Postcard</title>
<link rel="stylesheet" href="https://fonts.googleapis.com/css2?family=Oswald:wght@700&family=Lato:ital,wght@0,400;0,700;0,900;1,300&display=swap">
<style>
  :root {
    --page-bg: #e4e4e4;
    --royal-blue: #2340a6;
    --deep-blue: #1b2f8a;
    --sun-yellow: #ffd63d;
    --orange-light: #ffc23a;
    --orange: #f59a23;
    --orange-deep: #ee7f16;
    --hot-pink: #ec2a8f;
    --lime: #8cc63f;
    --lime-light: #b6e04a;
    --ink: #1d1d1d;
    --white: #ffffff;
  }
  * { margin: 0; padding: 0; box-sizing: border-box; }
  html, body { width: 1200px; height: 982px; overflow: hidden; }
  body { background: var(--page-bg); position: relative; font-family: "Lato", sans-serif; }

  .postcard {
    position: absolute; left: 50px; top: 63px;
    width: 1100px; height: 856px; overflow: hidden;
    background: var(--orange);
  }
  .postcard-art { position: absolute; inset: 0; width: 1100px; height: 856px; }

  .experience { position: absolute; left: 38px; top: 32px; text-transform: uppercase; }
  .experience-years { color: var(--sun-yellow); font-weight: 900; font-size: 34px; letter-spacing: .5px; line-height: 1.1; }
  .experience-label { color: var(--white); font-weight: 700; font-size: 26px; line-height: 1.3; }

  .headline { position: absolute; left: 38px; top: 218px; line-height: 1; }
  .headline-strong { display: block; font-family: "Oswald", sans-serif; font-weight: 700; font-size: 80px; color: var(--ink); letter-spacing: 1px; }
  .headline-soft { display: block; margin-top: 8px; font-weight: 300; font-style: italic; font-size: 84px; color: var(--white); letter-spacing: 1px; }

  .intro {
    position: absolute; left: 40px; top: 432px; width: 362px;
    font-size: 21.5px; line-height: 25px; color: var(--ink);
    text-align: justify;
  }

  .badge-text {
    position: absolute; left: 667px; top: 500px; width: 240px;
    text-align: center; text-transform: uppercase; line-height: 1.05;
  }
  .badge-lead { color: var(--hot-pink); font-size: 21px; font-weight: 700; }
  .badge-main { color: var(--ink); font-size: 40px; font-weight: 900; margin-top: 6px; }
  .badge-tail { color: var(--hot-pink); font-size: 34px; font-weight: 900; margin-top: 4px; }

  .contact {
    position: absolute; left: 46px; top: 776px;
    display: flex; align-items: center; gap: 38px;
    color: var(--white); font-size: 32px; font-weight: 700;
  }
  .contact-web { display: flex; align-items: center; gap: 10px; }
  .contact-web svg { width: 22px; height: 22px; }
</style>
</head>
<body>
  <div class="postcard">
    <svg class="postcard-art" viewBox="0 0 1100 856" xmlns="http://www.w3.org/2000/svg">
      <defs>
        <radialGradient id="sunGlow" cx="640" cy="520" r="700" gradientUnits="userSpaceOnUse">
          <stop offset="0" stop-color="#ffe066"/>
          <stop offset="0.35" stop-color="#ffbf35"/>
          <stop offset="0.75" stop-color="#f59a23"/>
          <stop offset="1" stop-color="#ee7f16"/>
        </radialGradient>
        <linearGradient id="blueBand" x1="0" y1="0" x2="1" y2="1">
          <stop offset="0" stop-color="#2a4cc0"/>
          <stop offset="1" stop-color="#1b2f8a"/>
        </linearGradient>
        <linearGradient id="photoTone" x1="0" y1="0" x2="1" y2="1">
          <stop offset="0" stop-color="#e9d3b6"/>
          <stop offset="0.5" stop-color="#c9a07a"/>
          <stop offset="1" stop-color="#efe4d6"/>
        </linearGradient>
        <radialGradient id="badgeFill" cx="0.5" cy="0.45" r="0.6">
          <stop offset="0" stop-color="#c9ec5e"/>
          <stop offset="1" stop-color="#86c534"/>
        </radialGradient>
      </defs>

      <rect class="sunburst" width="1100" height="856" fill="url(#sunGlow)"/>

      <!-- top band -->
      <path class="top-band" d="M0 0 H700 V140 C560 150 300 160 0 165 Z" fill="url(#blueBand)"/>
      <path class="top-stripe-pink" d="M0 165 C300 160 560 150 700 140" fill="none" stroke="var(--hot-pink)" stroke-width="8"/>
      <path class="top-stripe-lime" d="M0 176 C300 171 560 161 700 151" fill="none" stroke="var(--lime)" stroke-width="8"/>

      <!-- photo with ring frame -->
      <ellipse class="ring-pink" cx="870" cy="100" rx="446" ry="414" fill="var(--hot-pink)"/>
      <ellipse class="ring-lime" cx="870" cy="100" rx="434" ry="402" fill="var(--lime)"/>
      <ellipse class="ring-yellow" cx="870" cy="100" rx="420" ry="388" fill="var(--sun-yellow)"/>
      <ellipse class="ring-white" cx="870" cy="100" rx="412" ry="380" fill="var(--white)"/>
      <g role="img" aria-label="Photo: a caring adult taking a sick child's temperature while the child rests under a blanket">
        <ellipse class="photo-area" cx="870" cy="100" rx="406" ry="374" fill="url(#photoTone)"/>
      </g>

      <!-- bottom band -->
      <path class="bottom-stripe-pink" d="M0 742 C300 660 760 660 1100 752" fill="none" stroke="var(--hot-pink)" stroke-width="9"/>
      <path class="bottom-stripe-lime" d="M0 756 C300 674 760 674 1100 766" fill="none" stroke="var(--lime)" stroke-width="9"/>
      <path class="bottom-stripe-white" d="M0 766 C300 684 760 684 1100 776" fill="none" stroke="var(--white)" stroke-width="5"/>
      <path class="bottom-band" d="M0 770 C300 688 760 688 1100 780 V856 H0 Z" fill="url(#blueBand)"/>

      <!-- scalloped badge -->
      <g class="badge" transform="translate(787 560)">
        <g fill="var(--white)">
          <circle r="122"/>
          <circle cx="0" cy="-106" r="34"/><circle cx="53" cy="-92" r="34"/><circle cx="92" cy="-53" r="34"/>
          <circle cx="106" cy="0" r="34"/><circle cx="92" cy="53" r="34"/><circle cx="53" cy="92" r="34"/>
          <circle cx="0" cy="106" r="34"/><circle cx="-53" cy="92" r="34"/><circle cx="-92" cy="53" r="34"/>
          <circle cx="-106" cy="0" r="34"/><circle cx="-92" cy="-53" r="34"/><circle cx="-53" cy="-92" r="34"/>
        </g>
        <g fill="url(#badgeFill)">
          <circle r="116"/>
          <circle cx="0" cy="-104" r="29"/><circle cx="52" cy="-90" r="29"/><circle cx="90" cy="-52" r="29"/>
          <circle cx="104" cy="0" r="29"/><circle cx="90" cy="52" r="29"/><circle cx="52" cy="90" r="29"/>
          <circle cx="0" cy="104" r="29"/><circle cx="-52" cy="90" r="29"/><circle cx="-90" cy="52" r="29"/>
          <circle cx="-104" cy="0" r="29"/><circle cx="-90" cy="-52" r="29"/><circle cx="-52" cy="-90" r="29"/>
        </g>
      </g>
    </svg>

    <div class="experience">
      <div class="experience-years">Over 14 Years</div>
      <div class="experience-label">Child Care Experience</div>
    </div>

    <h1 class="headline">
      <span class="headline-strong">COZY HOUR</span>
      <span class="headline-soft">HELPER</span>
    </h1>

    <p class="intro">I would like to help out those parents in need who have pressing schedules and a sick child at home. I can bring relief to stressed parents who really want to stay home to take care of their child, but cant due to their work obligations and priorities.</p>

    <div class="badge-text">
      <div class="badge-lead">But you must go</div>
      <div class="badge-main">To Work</div>
      <div class="badge-tail">Today</div>
    </div>

    <div class="contact">
      <span class="contact-name">Mara Dellwood</span>
      <span class="contact-phone">(206) 555-0148</span>
      <span class="contact-web">
        <svg viewBox="0 0 24 24" aria-hidden="true"><circle cx="12" cy="12" r="10" fill="var(--sun-yellow)"/><path d="M2 12h20M12 2c3 3 3 17 0 20M12 2c-3 3-3 17 0 20" stroke="var(--deep-blue)" stroke-width="1.6" fill="none"/></svg>
        www.sitternest.com/marad214/cc
      </span>
    </div>
  </div>
</body>
</html>
```